Stylish Business Cards Wanted

- DOUBLE SIDED Design Required -

High end, edgy cards for a corporate and personal stylist. Must include logo,
Name: Belinda Harwick
Title: Director and Stylist
telephone : +61 8 7142 5809
email: belinda@theloombriefing.example
website: theloombriefing.example
Tag: Corporate Workwear & Uniform Specialist | Personal Stylist
Would like nice icons for telephone, email, website

Target Market(s)

Businesses wanting stylish uniforms, people wanting stylish wardrobes

Industry/Entity Type

Corporate Workwear Stylist

Contact Information for Business Card

I would like black, white and gold foiling incorporated in the design - possibly a touch of the other colours on my branding guide attached Name: Belinda Harwick Title: Director and Stylist telephone : +61 8 7142 5809 email: belinda@theloombriefing.example website: theloombriefing.example Tag: Corporate Workwear & Uniform Specialist | Personal Stylist Would like nice icons for telephone, email, website

Font styles to use
Other font styles liked:
• Raleway

Colors

Designer to choose colors to be used in the design.

Requirements
Must have
• Gold foil accents

```html
<!DOCTYPE html>
<html lang="en">
<head>
<meta charset="utf-8">
<title>The Loom Briefing – Business Card</title>
<link rel="stylesheet" href="https://fonts.googleapis.com/css2?family=Roboto:wght@400&family=Dancing+Script:wght@500&family=Kaushan+Script&display=swap">
<style>
  :root {
    --page-bg: #e9e6e1;
    --card-top: #f7f7f6;
    --card-bottom: #e4e4e2;
    --navy: #1f2740;
    --gold: #c9993a;
    --gold-light: #e2bd62;
    --gold-dark: #a9782a;
    --ink: #1b1b1f;
    --white: #ffffff;
  }
  html, body {
    margin: 0;
    width: 1200px;
    height: 1054px;
    overflow: hidden;
    background: var(--page-bg);
  }
  .card {
    position: absolute;
    left: 100px;
    top: 224px;
    width: 1000px;
    height: 605px;
    border-radius: 28px;
    overflow: hidden;
    background: linear-gradient(160deg, var(--card-top), var(--card-bottom));
    box-shadow: 0 12px 40px rgba(0,0,0,0.18);
    font-family: "Roboto", Arial, sans-serif;
  }
  .card-shapes {
    position: absolute;
    inset: 0;
  }
  .brand-name {
    position: absolute;
    left: 30px;
    width: 370px;
    top: 266px;
    text-align: center;
    color: var(--white);
    font-family: "Roboto", Arial, sans-serif;
    font-weight: 400;
    font-size: 38px;
    letter-spacing: 1px;
    margin: 0;
  }
  .contact-block {
    position: absolute;
    left: 507px;
    top: 148px;
  }
  .person-name {
    margin: 0;
    font-family: "Dancing Script", cursive;
    font-weight: 500;
    font-size: 52px;
    color: var(--gold);
    line-height: 1;
  }
  .person-title {
    margin: 12px 0 0;
    font-size: 26px;
    color: var(--ink);
  }
  .contact-list {
    list-style: none;
    margin: 36px 0 0;
    padding: 0;
  }
  .contact-list li {
    display: flex;
    align-items: center;
    gap: 18px;
    height: 42px;
    font-size: 26px;
    color: var(--ink);
  }
  .contact-list svg {
    width: 25px;
    height: 25px;
    flex: none;
  }
  .tagline {
    position: absolute;
    left: 340px;
    top: 516px;
    width: 660px;
    height: 55px;
    display: flex;
    align-items: center;
    justify-content: space-between;
    padding: 0 30px 0 22px;
    box-sizing: border-box;
    font-family: "Kaushan Script", cursive;
    font-size: 24px;
    color: var(--ink);
  }
</style>
</head>
<body>
  <div class="card">
    <svg class="card-shapes" viewBox="0 0 1000 605" width="1000" height="605" aria-hidden="true">
      <defs>
        <linearGradient id="goldFoil" x1="0" y1="0" x2="1" y2="1">
          <stop offset="0" stop-color="var(--gold-dark)"/>
          <stop offset="0.45" stop-color="var(--gold-light)"/>
          <stop offset="1" stop-color="var(--gold)"/>
        </linearGradient>
      </defs>
      <path class="gold-curve" d="M415 0 H423 C484 175 484 430 362 605 H330 C470 420 470 170 415 0 Z" fill="url(#goldFoil)"/>
      <path class="navy-panel" d="M0 0 H415 C470 170 470 420 330 605 H0 Z" fill="var(--navy)"/>
      <rect class="tag-band" x="340" y="516" width="660" height="55" fill="url(#goldFoil)"/>
    </svg>

    <p class="brand-name">The Loom Briefing</p>

    <div class="contact-block">
      <h1 class="person-name">Belinda Harwick</h1>
      <p class="person-title">Director and Stylist</p>
      <ul class="contact-list">
        <li>
          <svg viewBox="0 0 24 24" fill="none" stroke="var(--gold)" stroke-width="1.6" aria-hidden="true">
            <circle cx="12" cy="12" r="10"/>
            <path d="M8.5 7.5l1.8-.4 1 2.4-1.2 1a6 6 0 0 0 3.4 3.4l1-1.2 2.4 1-.4 1.8c-4.5.4-8.4-3.5-8-8z" fill="var(--gold)" stroke="none"/>
          </svg>
          <span>+61 8 7142 5809</span>
        </li>
        <li>
          <svg viewBox="0 0 24 24" fill="none" stroke="var(--gold)" stroke-width="1.6" aria-hidden="true">
            <rect x="3" y="5.5" width="18" height="13" rx="1"/>
            <path d="M3 6l9 7 9-7"/>
          </svg>
          <span>belinda@theloombriefing.example</span>
        </li>
        <li>
          <svg viewBox="0 0 24 24" fill="none" stroke="var(--gold)" stroke-width="1.6" aria-hidden="true">
            <circle cx="12" cy="12" r="9.5"/>
            <ellipse cx="12" cy="12" rx="4" ry="9.5"/>
            <path d="M2.5 12h19M4 7h16M4 17h16"/>
          </svg>
          <span>www.theloombriefing.example</span>
        </li>
      </ul>
    </div>

    <div class="tagline">
      <span>Corporate Workwear &amp; Uniform Specialist</span>
      <span>Personal Stylist</span>
    </div>
  </div>
</body>
</html>
```